Creative, fresh business card design for Ripplecraft Facades

We need a fresh, creative business card design for Ripplecraft Facades. We are the manufacturer of Ripplecraft Facades in Australia. Wall panels are 2400 x 1200mm panels made from MDF and feature 3D patterns on the face of the panel. The colours to be used are green, silver/grey and white RGB
Red 187
Green 207
Blue 65.

An idea is to possibly use a watermark of one of our designs as a background (like on the "Grids" design on the left hand side of page 2 of our brochure).

Target Market(s)

Interior designers, architects, builders and home renovators

Industry/Entity Type

Business

Contact Information for Business Card

Details to go on the card are:
Our logo (attached),
Slogan: "Decorative panels for interiors and exteriors",
Contact name,
Position,
Mobile phone number,
Business address,
Business phone,
Business fax,
Website and
Email address.

I have attached a few images of our panels and our brochure for reference.

The colours of the business card should feature our logo colours which are: RGB
Red 187
Green 207
Blue 65

Requirements
Must have
• Very modern fonts and design. Some of the designs shown especially the "Prisms" design which is a popular design.
Nice to have
• Creative but simple design. Very contemporary.
Should not have
• Anything ornate or old fashioned.

```html
<!DOCTYPE html>
<html lang="en">
<head>
<meta charset="utf-8">
<title>Ripplecraft Facades — Business Card</title>
<link rel="stylesheet" href="https://fonts.googleapis.com/css2?family=Arimo:wght@400;700&display=swap">
<style>
  :root {
    --brand-green: #bbcf41;
    --brand-green-light: #c8da5a;
    --band-grey: #9a9a9f;
    --band-grey-light: #b4b4b8;
    --ink: #2f2f2f;
    --ink-soft: #3d3d3d;
    --tag-grey: #8d8d90;
    --paper: #f6f5f3;
    --paper-shade: #e6e5e2;
    --stage: #e4e1dc;
  }
  * { margin: 0; padding: 0; box-sizing: border-box; }
  html, body {
    width: 1200px; height: 987px; overflow: hidden;
    background: var(--stage);
    font-family: "Arimo", Arial, sans-serif;
  }
  .canvas { position: relative; width: 1200px; height: 987px; }

  .card {
    position: absolute; left: 292px; width: 616px; height: 350px;
    overflow: hidden;
    box-shadow: 0 3px 10px rgba(0,0,0,.25);
  }
  .card--front { top: 130px; }
  .card--back { top: 505px; }

  .texture { position: absolute; inset: 0; }
  .card--front .texture {
    background: radial-gradient(circle at 40% 40%, var(--brand-green-light), var(--brand-green) 70%);
  }
  .card--back .texture {
    background: radial-gradient(circle at 50% 45%, var(--paper), var(--paper-shade) 90%);
  }

  .contact { position: absolute; left: 26px; top: 80px; color: var(--ink-soft); }
  .contact__name { font-size: 22px; font-weight: 700; letter-spacing: .5px; color: var(--ink); line-height: 1; }
  .contact__role { font-size: 18px; margin-top: 5px; line-height: 1; }
  .contact__address { font-size: 16px; line-height: 21px; margin-top: 21px; }
  .contact__lines { list-style: none; margin-top: 10px; font-size: 16px; line-height: 24px; }
  .contact__lines li { display: flex; align-items: center; gap: 6px; }
  .contact__lines svg { width: 14px; height: 14px; fill: var(--ink); flex: none; }

  .brand-name--front {
    position: absolute; right: 22px; top: 168px;
    text-align: right; color: var(--ink);
    font-weight: 700; font-size: 46px; line-height: 50px; letter-spacing: -1px;
  }

  .web-band {
    position: absolute; left: 0; right: 0; bottom: 0; height: 52px;
    background: linear-gradient(var(--band-grey-light), var(--band-grey));
    border-top: 2px solid #f2f2f2;
    display: flex; align-items: center; padding-left: 32px;
    font-size: 16px; letter-spacing: 4px; color: var(--ink-soft);
  }

  .brand-lockup {
    position: absolute; left: 0; right: 0; top: 118px;
    display: flex; flex-direction: column; align-items: center;
  }
  .brand-name--back {
    display: flex; align-items: center; gap: 12px;
    font-size: 34px; font-weight: 700; color: var(--ink); letter-spacing: -.5px;
  }
  .brand-mark { width: 26px; height: 26px; background: var(--brand-green); }
  .tagline {
    margin-top: 30px; text-align: center;
    font-size: 13.5px; line-height: 19px; letter-spacing: 2.2px; color: var(--tag-grey);
  }
</style>
</head>
<body>
<main class="canvas">

  <section class="card card--front" aria-label="Business card front">
    <div class="texture" role="img" aria-label="Embossed concentric ripple panel pattern in green"></div>

    <div class="contact">
      <p class="contact__name">DANIEL HART</p>
      <p class="contact__role">CEO &amp; Founder</p>
      <p class="contact__address">42 Kelso Street<br>Geelong, Victoria 3220</p>
      <ul class="contact__lines">
        <li>
          <svg viewBox="0 0 16 16" aria-label="Phone"><path d="M3.6 1.2l2.3 2.6-1.3 1.9c.9 2.2 2.6 3.9 4.7 4.9l1.9-1.3 2.6 2.3-1.2 2.6C7.6 14.5 1.5 8.4 1 2.4z"/></svg>
          (555) 214-7730
        </li>
        <li>
          <svg viewBox="0 0 16 16" aria-label="Fax"><rect x="4" y="1" width="8" height="5"/><rect x="1" y="6" width="14" height="6" rx="1"/><rect x="4" y="10" width="8" height="5" fill="#e8e8e8"/></svg>
          (555) 214-7731
        </li>
        <li>
          <svg viewBox="0 0 16 16" aria-label="Email"><path d="M1 3h14v10H1z"/><path d="M1 3l7 6 7-6" fill="none" stroke="#dfe9a0" stroke-width="1.4"/></svg>
          dhart@ripplecraftfacades.com
        </li>
      </ul>
    </div>

    <p class="brand-name--front">Ripplecraft<br>Facades</p>

    <div class="web-band">WWW.RIPPLECRAFTFACADES.COM</div>
  </section>

  <section class="card card--back" aria-label="Business card back">
    <div class="texture" role="img" aria-label="Embossed concentric ripple panel pattern in white"></div>

    <div class="brand-lockup">
      <p class="brand-name--back"><span class="brand-mark"></span>Ripplecraft Facades</p>
      <p class="tagline">decorative panels for<br>interiors &amp; landscapes</p>
    </div>
  </section>

</main>
</body>
</html>
```